New Supplement Product Website for Cephavora

I need a website for a new migraine supplement product called Quimbrosel. It is a powder formula meant to stir into water. I would like a website that works for online and mobile. This is a natural and non-prescription solution for migraine sufferers. Each supplement included in this product is a natural and widely used supplement for everyday use (list provided upon selection). We have a logo and an idea of what the bottles will look like. Product to be released this summer. I would like the website to be sophisticated and clinical while also having a straight-to-consumer appeal. (Lantern Probiotics, Harbor Sprouts, Velbry) The bottle will look similar to the Velbry product bottles (white bottle with logos). It will be a wider container to carry the orange/passion fruit supplement. I would like one page describing the product and ingredients, one page with the option to buy the product, one page with the story/team. Very similar to Harbor Sprouts or Lantern or Velbry website.

Target Market(s)

Clinicians as well as women ages 18-55. Want to appeal to all while keeping this in mind

Industry/Entity Type

Health and Wellness, Supplements

Coding

Coded - Design and coding required

Number of Pages Required

4 page

Font styles to use
Serif
Sans Serif

Colors
0094D4
00A9DD
6FCCEA
C7EBF8
E9F6FB
00AB8E
00BBA5
67D7C9
C6EFE9
E9F9F6

Requirements
Must have
• About Page, Shop Page, review space for product, Science Page (see lantern website), place for twitter instagram pages

```html
<!DOCTYPE html>
<html lang="en">
<head>
<meta charset="utf-8">
<title>Quimbrosel — Natural Migraine Support</title>
<link rel="stylesheet" href="https://fonts.googleapis.com/css2?family=Baloo+2:wght@700;800&family=Lato:wght@400;700&display=swap">
<style>
:root{
  --green:#16a07e;
  --green-light:#5fd3b8;
  --maroon:#9a0c3b;
  --ink:#1d1d1d;
  --text:#333;
  --light:#f0f1f3;
  --card:#f3f5f7;
  --footer:#222324;
  --star:#e0a21b;
}
*{box-sizing:border-box;margin:0;padding:0}
html,body{width:1200px;height:3665px;overflow:hidden}
body{position:relative;font-family:"Lato",sans-serif;color:var(--text);background:#fff}
.heading{font-family:"Baloo 2",sans-serif;font-weight:800;color:var(--ink);letter-spacing:.5px}
a{color:inherit;text-decoration:none}

/* header */
.site-header{position:absolute;top:0;left:0;width:1200px;height:74px;background:#fff;z-index:3}
.brand-box{position:absolute;left:110px;top:0;width:165px;height:95px;background:#fff;display:flex;align-items:center;justify-content:center;gap:8px;z-index:4}
.brand-dot{width:14px;height:14px;border-radius:50%;background:var(--green)}
.brand-name{font-size:24px;color:var(--green)}
.nav a{position:absolute;top:28px;font-size:15px;color:#222;text-transform:uppercase}
.nav a.active{color:var(--green)}
.nav a.active::after{content:"";position:absolute;left:0;right:0;bottom:-6px;height:2px;background:var(--green)}
.cart-badge{position:absolute;left:918px;top:21px;width:14px;height:14px;border-radius:50%;background:var(--green);color:#fff;font-size:9px;text-align:center;line-height:14px}
.btn-login{position:absolute;left:965px;top:13px;width:123px;height:43px;border-radius:22px;background:var(--maroon);color:#fff;font-weight:700;font-size:15px;display:flex;align-items:center;justify-content:center;gap:8px}

/* photo placeholders */
.photo{background-color:#a89a8c}

/* hero */
.hero{position:absolute;top:74px;left:0;width:1200px;height:598px;
  background:
    linear-gradient(90deg,rgba(40,30,22,.55) 0%,rgba(40,30,22,.2) 40%,rgba(0,0,0,0) 60%),
    radial-gradient(ellipse 260px 300px at 640px 210px,#8a5a3f 0%,rgba(138,90,63,0) 100%),
    radial-gradient(ellipse 420px 200px at 620px 520px,#e8e6e2 0%,rgba(232,230,226,0) 100%),
    radial-gradient(ellipse 300px 260px at 1000px 330px,#cfcdca 0%,rgba(207,205,202,0) 100%),
    linear-gradient(100deg,#5b4a3a 0%,#8a7662 35%,#a9987f 55%,#bdb4a8 80%,#cfcac3 100%)}
.hero-title{position:absolute;left:108px;top:178px;font-size:82px;color:#fff;line-height:1}
.hero-sub{position:absolute;left:111px;top:278px;width:410px;font-size:15px;line-height:26px;color:#fff}
.btn-primary{position:absolute;height:48px;border-radius:24px;background:var(--maroon);color:#fff;font-weight:700;font-size:15px;display:flex;align-items:center;justify-content:center;gap:10px}
.slide-arrow{position:absolute;top:280px;width:38px;height:38px;border-radius:50%;background:#fff;display:flex;align-items:center;justify-content:center}

/* products */
.section-title{position:absolute;left:0;width:1200px;text-align:center;font-size:32px}
.product-card{position:absolute;top:814px;width:213px;height:281px;background:var(--card);border:1px solid #e3e6e9;text-align:center}
.product-card.featured{background:#fff;box-shadow:0 2px 10px rgba(0,0,0,.12)}
.bottle{position:absolute;left:66px;top:20px;width:80px;height:134px;border-radius:10px;
  background:radial-gradient(ellipse 30px 55px at 40% 55%,#fff 0%,rgba(255,255,255,0) 100%),linear-gradient(90deg,#d6dadd,#f7f8f9 45%,#dde1e3)}
.product-name{position:absolute;left:0;right:0;top:166px;font-weight:700;font-size:15px;color:#222}
.product-desc{position:absolute;left:0;right:0;top:189px;font-size:14.5px;color:#333}
.stars{position:absolute;left:0;right:0;top:212px;color:var(--star);font-size:15px;letter-spacing:2px}
.add-cart{position:absolute;left:0;right:0;top:240px;font-weight:700;font-size:14.5px;color:var(--green);display:flex;justify-content:center;align-items:center;gap:10px}
.add-cart span{text-decoration:underline}
.heart{position:absolute;right:18px;top:20px}

/* about */
.about{position:absolute;top:1180px;left:0;width:1200px;height:453px;background:var(--light)}
.about-title{position:absolute;left:142px;top:46px;font-size:28px}
.about-text{position:absolute;left:142px;top:96px;width:480px;font-size:14.5px;line-height:25.8px;color:#333}
.about-ring{position:absolute;left:690px;top:38px;width:376px;height:376px;border-radius:50%;border:4px solid var(--green);border-left-color:transparent;border-bottom-color:transparent;transform:rotate(60deg)}
.about-photo{position:absolute;left:693px;top:43px;width:366px;height:366px;border-radius:50%;
  background:
    radial-gradient(ellipse 90px 110px at 58% 30%,#c99c7e 0%,rgba(201,156,126,0) 100%),
    radial-gradient(ellipse 150px 120px at 50% 78%,#fbfbfb 0%,rgba(251,251,251,0) 100%),
    radial-gradient(ellipse 120px 180px at 15% 40%,#9b8e80 0%,rgba(155,142,128,0) 100%),
    linear-gradient(135deg,#d9d4ce,#ece9e5 60%,#cfc7be)}

/* team */
.member{position:absolute;top:1768px;width:204px}
.member-photo{width:204px;height:191px}
.member-name{margin-top:14px;font-size:15px;font-weight:700;color:#222;text-transform:uppercase}
.member-role{margin-top:8px;font-size:14.5px;line-height:26px;color:#333}
.member-featured{position:absolute;left:599px;top:1768px;width:231px;height:320px;background:var(--green);border:2px solid var(--green-light);outline:2px solid rgba(255,255,255,.85);outline-offset:-9px;color:#fff}
.member-featured .avatar{position:absolute;left:23px;top:28px;width:76px;height:76px;border-radius:50%;border:2px solid #fff;
  background:radial-gradient(circle at 50% 40%,#d4b29a 0%,#a88a73 35%,#6d6a68 70%,#c9cbcd 100%)}
.member-featured .member-name{position:absolute;left:23px;top:124px;margin:0;color:#fff}
.member-featured .member-role{position:absolute;left:23px;top:156px;width:195px;margin:0;color:#fff}
.socials-inline{position:absolute;left:22px;top:270px;display:flex;gap:20px}
.socials-inline span,.footer-social{display:flex;align-items:center;justify-content:center}

/* testimonials */
.testimonials{position:absolute;top:2174px;left:0;width:1200px;height:439px;background:linear-gradient(180deg,#eceeef,#f7f8f8 50%,#eceeef)}
.testimonial-text{position:absolute;left:158px;top:118px;width:884px;text-align:center;font-size:14.5px;line-height:25.8px;color:#333}
.t-avatar{position:absolute;left:565px;top:274px;width:68px;height:68px;border-radius:50%;
  background:radial-gradient(circle at 50% 42%,#c49a7e 0%,#8a6a55 38%,#3f4a57 72%,#dfe3e6 100%)}
.t-name{position:absolute;left:0;width:1200px;top:360px;text-align:center;font-size:14.5px;color:#333}
.t-name b{color:#222}

/* gallery */
.gallery-tile{position:absolute}
.gal-badge{position:absolute;left:50%;top:50%;width:32px;height:32px;margin:-16px 0 0 -16px;border-radius:50%;background:var(--green);display:flex;align-items:center;justify-content:center}

/* footer */
.site-footer{position:absolute;top:3268px;left:0;width:1200px;height:397px;background:var(--footer);color:#fff}
.footer-brand{position:absolute;left:110px;top:92px;font-size:30px;color:var(--green);display:flex;align-items:center;gap:10px}
.footer-brand i{display:block;width:20px;height:20px;border-radius:50%;background:var(--green)}
.footer-tag{position:absolute;left:110px;top:170px;width:240px;font-size:14px;line-height:23px}
.footer-follow{position:absolute;left:110px;top:228px;font-weight:700;font-size:14.5px;text-decoration:underline}
.footer-social{position:absolute;top:266px;width:34px;height:34px;border-radius:50%;border:1.5px solid #fff}
.col-title{position:absolute;top:62px;font-weight:700;font-size:15px;text-decoration:underline;text-transform:uppercase}
.col-list{position:absolute;top:98px;list-style:none;font-size:14.5px}
.col-list li{height:38.5px}
.col-list li::before{content:"»";margin-right:12px}
.contact-row{position:absolute;left:886px;display:flex;align-items:center;gap:14px;font-size:14.5px;line-height:23px}
.contact-icon{width:32px;height:32px;border-radius:50%;border:1.5px solid #fff;display:flex;align-items:center;justify-content:center;flex:none}
.footer-rule{position:absolute;left:110px;top:345px;width:980px;height:1px;background:#4a4b4c}
.copyright{position:absolute;left:0;width:1200px;top:362px;text-align:center;font-size:14px}
</style>
</head>
<body>

<header class="site-header">
  <div class="brand-box"><span class="brand-dot"></span><span class="brand-name">quimbrosel</span></div>
  <nav class="nav">
    <a class="active" style="left:317px" href="#">Home</a>
    <a style="left:384px" href="#">About</a>
    <a style="left:458px" href="#">Shop</a>
    <a style="left:521px" href="#">Review Space For Product</a>
    <a style="left:761px" href="#">Science</a>
    <a style="left:856px" href="#"><svg width="16" height="14" viewBox="0 0 16 14" style="vertical-align:-2px;margin-right:4px"><path d="M0 1h3l2 8h9l2-6H4" fill="none" stroke="#16a07e" stroke-width="2"/><circle cx="6" cy="12" r="1.5" fill="#16a07e"/><circle cx="13" cy="12" r="1.5" fill="#16a07e"/></svg>Cart</a>
  </nav>
  <span class="cart-badge">0</span>
  <a class="btn-login" href="#">LOGIN <svg width="12" height="14" viewBox="0 0 12 14"><rect x="1" y="6" width="10" height="8" rx="1" fill="#fff"/><path d="M3 6V4a3 3 0 0 1 6 0v2" fill="none" stroke="#fff" stroke-width="2"/></svg></a>
</header>

<section class="hero photo" role="img" aria-label="Woman at a laptop holding her temple with a headache, in a softly lit home office">
  <h1 class="heading hero-title">Quimbrosel</h1>
  <p class="hero-sub">Lorem ipsum dolor sit amet, consectetur adipiscing elit sed tempor incididunt laboredolore sit magna ut consectetur.</p>
  <a class="btn-primary" style="left:111px;top:354px;width:171px" href="#">GET STARTED <svg width="16" height="16" viewBox="0 0 16 16"><circle cx="8" cy="8" r="7" fill="#fff"/><path d="M6 4l4 4-4 4" fill="none" stroke="#9a0c3b" stroke-width="2"/></svg></a>
  <span class="slide-arrow" style="left:41px"><svg width="12" height="14" viewBox="0 0 12 14"><path d="M8 2L3 7l5 5" fill="none" stroke="#222" stroke-width="2"/></svg></span>
  <span class="slide-arrow" style="left:1120px"><svg width="12" height="14" viewBox="0 0 12 14"><path d="M4 2l5 5-5 5" fill="none" stroke="#222" stroke-width="2"/></svg></span>
</section>

<h2 class="heading section-title" style="top:748px">Our Products</h2>

<article class="product-card" style="left:142px">
  <div class="bottle" role="img" aria-label="White supplement bottle"></div>
  <div class="product-name">PRODUCTS TITTLE</div>
  <div class="product-desc">consectetur adipiscing elit</div>
  <div class="stars">★★★★★</div>
  <a class="add-cart" href="#"><span>ADD TO CART</span><svg width="16" height="14" viewBox="0 0 16 14"><path d="M0 1h3l2 8h9l2-6H4" fill="#16a07e" stroke="#16a07e" stroke-width="2"/><circle cx="6" cy="12" r="1.5" fill="#16a07e"/><circle cx="13" cy="12" r="1.5" fill="#16a07e"/></svg></a>
</article>
<article class="product-card featured" style="left:376px">
  <svg class="heart" width="16" height="14" viewBox="0 0 16 14"><path d="M8 14L1.5 7.5A4 4 0 0 1 8 2.5a4 4 0 0 1 6.5 5z" fill="#e2163f"/></svg>
  <div class="bottle" role="img" aria-label="White supplement bottle"></div>
  <div class="product-name">PRODUCTS TITTLE</div>
  <div class="product-desc">consectetur adipiscing elit</div>
  <div class="stars">★★★★★</div>
  <a class="add-cart" href="#"><span>ADD TO CART</span><svg width="16" height="14" viewBox="0 0 16 14"><path d="M0 1h3l2 8h9l2-6H4" fill="#16a07e" stroke="#16a07e" stroke-width="2"/><circle cx="6" cy="12" r="1.5" fill="#16a07e"/><circle cx="13" cy="12" r="1.5" fill="#16a07e"/></svg></a>
</article>
<article class="product-card" style="left:611px">
  <div class="bottle" role="img" aria-label="White supplement bottle"></div>
  <div class="product-name">PRODUCTS TITTLE</div>
  <div class="product-desc">consectetur adipiscing elit</div>
  <div class="stars">★★★★★</div>
  <a class="add-cart" href="#"><span>ADD TO CART</span><svg width="16" height="14" viewBox="0 0 16 14"><path d="M0 1h3l2 8h9l2-6H4" fill="#16a07e" stroke="#16a07e" stroke-width="2"/><circle cx="6" cy="12" r="1.5" fill="#16a07e"/><circle cx="13" cy="12" r="1.5" fill="#16a07e"/></svg></a>
</article>
<article class="product-card" style="left:845px">
  <div class="bottle" role="img" aria-label="White supplement bottle"></div>
  <div class="product-name">PRODUCTS TITTLE</div>
  <div class="product-desc">consectetur adipiscing elit</div>
  <div class="stars">★★★★★</div>
  <a class="add-cart" href="#"><span>ADD TO CART</span><svg width="16" height="14" viewBox="0 0 16 14"><path d="M0 1h3l2 8h9l2-6H4" fill="#16a07e" stroke="#16a07e" stroke-width="2"/><circle cx="6" cy="12" r="1.5" fill="#16a07e"/><circle cx="13" cy="12" r="1.5" fill="#16a07e"/></svg></a>
</article>

<section class="about">
  <h2 class="heading about-title">About Us</h2>
  <p class="about-text">Lorem ipsum dolor sit amet, consectetur adipiscing elit, sed do eiusmod tempor incididunt ut labore et dolore magna aliqua.Ut enim aind minim veniam, quis nostrud exercitation ullamco laboris nisi aliquip commodo consequat.Duis aute irure dolor in reprehenderit in voluptate velit esse cillum dolore&nbsp; fugiat nullisa pariatur. Excepteur occaecat cupidatat noin proident, sunt&nbsp; culpa qui officia deserunt mollit anim est laborum Lorem ipsuem dolor sit amiet, consectetur adipiscing elitseid eiusmod tempeir incididunt ut labore et dolore magna aliqua.admt enim litseid eiusmond minim veniam, quis nostrud exercitation ullamco laboris nisi ut aliquip.</p>
  <a class="btn-primary" style="left:142px;top:350px;width:171px" href="#">GET STARTED <svg width="16" height="16" viewBox="0 0 16 16"><circle cx="8" cy="8" r="7" fill="#fff"/><path d="M6 4l4 4-4 4" fill="none" stroke="#9a0c3b" stroke-width="2"/></svg></a>
  <div class="about-photo" role="img" aria-label="Smiling woman in a white shirt resting her chin on her hands"></div>
  <div class="about-ring"></div>
</section>

<h2 class="heading section-title" style="top:1692px">Our Team</h2>

<div class="member" style="left:138px">
  <div class="member-photo" role="img" aria-label="Team member in a grey blazer in a bright office" style="background:radial-gradient(ellipse 60px 70px at 55% 38%,#c39a7c 0%,rgba(195,154,124,0) 100%),radial-gradient(ellipse 80px 70px at 55% 90%,#8d8e92 0%,rgba(141,142,146,0) 100%),linear-gradient(135deg,#e4e5e6,#cfd0d2 50%,#b6b4b1)"></div>
  <div class="member-name">Corin Vale</div>
  <div class="member-role">Lorem ipsum dolor sit amet consectetur ut adipiscing.</div>
</div>
<div class="member" style="left:369px">
  <div class="member-photo" role="img" aria-label="Team member in a striped shirt working at a laptop" style="background:radial-gradient(ellipse 55px 65px at 50% 30%,#b58a6c 0%,rgba(181,138,108,0) 100%),radial-gradient(ellipse 85px 70px at 50% 80%,#8fa9c9 0%,rgba(143,169,201,0) 100%),linear-gradient(135deg,#3b4650,#5d6a73 50%,#2b3238)"></div>
  <div class="member-name">Teodor Brisk</div>
  <div class="member-role">Lorem ipsum dolor sit amet consectetur ut adipiscing.</div>
</div>
<div class="member-featured">
  <div class="avatar" role="img" aria-label="Portrait of team member"></div>
  <div class="member-name">Nadir Olsen</div>
  <div class="member-role">Lorem ipsum&nbsp; consectetur adipiscing elit do eiusmod tempor incididunt ulabore tempiear dolore tempor.</div>
  <div class="socials-inline" aria-label="Social profiles">
    <span><svg width="14" height="14" viewBox="0 0 14 14"><circle cx="7" cy="7" r="6" fill="none" stroke="#fff" stroke-width="1.6"/><circle cx="7" cy="7" r="2" fill="#fff"/></svg></span>
    <span><svg width="14" height="14" viewBox="0 0 14 14"><circle cx="7" cy="7" r="6" fill="none" stroke="#fff" stroke-width="1.6"/><circle cx="7" cy="7" r="2" fill="#fff"/></svg></span>
    <span><svg width="14" height="14" viewBox="0 0 14 14"><circle cx="7" cy="7" r="6" fill="none" stroke="#fff" stroke-width="1.6"/><circle cx="7" cy="7" r="2" fill="#fff"/></svg></span>
    <span><svg width="14" height="14" viewBox="0 0 14 14"><circle cx="7" cy="7" r="6" fill="none" stroke="#fff" stroke-width="1.6"/><circle cx="7" cy="7" r="2" fill="#fff"/></svg></span>
  </div>
</div>
<div class="member" style="left:858px">
  <div class="member-photo" role="img" aria-label="Team member in a white blouse standing by a window" style="background:radial-gradient(ellipse 50px 60px at 55% 28%,#c79d82 0%,rgba(199,157,130,0) 100%),radial-gradient(ellipse 70px 80px at 55% 80%,#f3f4f6 0%,rgba(243,244,246,0) 100%),linear-gradient(90deg,#4e5356,#9aa0a3 35%,#d7d9da 70%,#b9bdc0)"></div>
  <div class="member-name">Liora</div>
  <div class="member-role">Lorem ipsum dolor sit amet consectetur ut adipiscing.</div>
</div>

<section class="testimonials">
  <h2 class="heading section-title" style="top:54px">Our Testimonials</h2>
  <p class="testimonial-text">Lorem ipsum dolor sit amet, consectetur adipiscing elit, sed do eiusmod tempor incididunt ut labore et dolore magna aliqua. Ut enim ad minim veniam, quis nostrud exercitation ullamco laboris nisi ut aliquip ex ea commodo consequat. Duis aute irure dolor in reprehenderit in voluptate velit esse cillum dolore eu fugiat nulla pariatur. Excepteur sint occaecat cupidatat non proident, sunt in culpa qui officia deserunt mollit anim id est Lorem ipsum dolor sit laborumLorem ipsum dolor sit amet, consectetur adipiscing elit, sed do eiusmod tempor incididunt ut labore et dolore magna aliqua. Ut enim ad minim veniam, quis nostrud exercitation</p>
  <div class="t-avatar" role="img" aria-label="Portrait of the reviewer"></div>
  <p class="t-name"><b>Teodor Brisk /</b>&nbsp; Lorem ipsum dolor sit</p>
</section>

<div class="gallery-tile" style="left:115px;top:2703px;width:237px;height:225px;background:radial-gradient(ellipse 90px 80px at 40% 45%,#c9a58c 0%,rgba(201,165,140,0) 100%),radial-gradient(ellipse 110px 70px at 50% 90%,#6f7276 0%,rgba(111,114,118,0) 100%),linear-gradient(160deg,#5f7d3e,#98a878 50%,#7a8a62)" role="img" aria-label="Older couple laughing outdoors"></div>
<div class="gallery-tile" style="left:369px;top:2703px;width:227px;height:225px;background:radial-gradient(ellipse 60px 60px at 50% 35%,#d8b88e 0%,rgba(216,184,142,0) 100%),radial-gradient(ellipse 70px 60px at 50% 65%,#b3373a 0%,rgba(179,55,58,0) 100%),radial-gradient(ellipse 80px 40px at 50% 92%,#4f6d95 0%,rgba(79,109,149,0) 100%),linear-gradient(135deg,#cdbda7,#ece4d8 50%,#d8cbb8)" role="img" aria-label="Woman in a red sweater holding her head on a sofa"></div>
<div class="gallery-tile" style="left:612px;top:2703px;width:228px;height:225px;background:radial-gradient(ellipse 60px 70px at 32% 35%,#7a4a30 0%,rgba(122,74,48,0) 100%),radial-gradient(ellipse 60px 70px at 68% 40%,#5e3f2c 0%,rgba(94,63,44,0) 100%),radial-gradient(ellipse 110px 60px at 50% 85%,#a9744f 0%,rgba(169,116,79,0) 100%),linear-gradient(135deg,#d6cdc2,#b9a892 60%,#8e7b68)" role="img" aria-label="Two women embracing and smiling"><span class="gal-badge"><svg width="14" height="14" viewBox="0 0 14 14"><circle cx="7" cy="7" r="5.5" fill="none" stroke="#fff" stroke-width="1.6"/><circle cx="7" cy="7" r="2" fill="#fff"/></svg></span></div>
<div class="gallery-tile" style="left:855px;top:2703px;width:228px;height:225px;background:radial-gradient(ellipse 70px 70px at 45% 30%,#6b3f33 0%,rgba(107,63,51,0) 100%),radial-gradient(ellipse 100px 80px at 55% 80%,#d4bfa4 0%,rgba(212,191,164,0) 100%),linear-gradient(135deg,#8a7b6e,#bfb09f 55%,#9b8876)" role="img" aria-label="Woman in a knit sweater holding her forehead"></div>
<div class="gallery-tile" style="left:115px;top:2957px;width:237px;height:226px;background:radial-gradient(ellipse 70px 70px at 55% 30%,#d8c9bc 0%,rgba(216,201,188,0) 100%),radial-gradient(ellipse 110px 80px at 45% 85%,#6e8fb8 0%,rgba(110,143,184,0) 100%),linear-gradient(135deg,#eae8e5,#d0d3d6 60%,#a9b4c0)" role="img" aria-label="Older woman rubbing her eyes in pain"></div>
<div class="gallery-tile" style="left:369px;top:2957px;width:227px;height:226px;background:radial-gradient(ellipse 60px 70px at 55% 35%,#8a5a3d 0%,rgba(138,90,61,0) 100%),radial-gradient(ellipse 90px 60px at 50% 85%,#e7dfe6 0%,rgba(231,223,230,0) 100%),linear-gradient(135deg,#4e3e33,#9a8370 50%,#6b5647)" role="img" aria-label="Group of friends laughing together"></div>
<div class="gallery-tile" style="left:612px;top:2957px;width:228px;height:226px;background:radial-gradient(ellipse 60px 70px at 50% 45%,#6d7380 0%,rgba(109,115,128,0) 100%),linear-gradient(180deg,#9e5b43 0%,#c8a18c 30%,#dcd6d0 60%,#3a8fd0 82%,#2f7dbd 100%)" role="img" aria-label="Woman sitting on a yoga mat holding her head"></div>
<div class="gallery-tile" style="left:855px;top:2957px;width:228px;height:226px;background:radial-gradient(ellipse 60px 80px at 30% 45%,#7d8fad 0%,rgba(125,143,173,0) 100%),radial-gradient(ellipse 60px 70px at 75% 55%,#a36d50 0%,rgba(163,109,80,0) 100%),linear-gradient(135deg,#3f352f,#7d6b5d 50%,#b8a592)" role="img" aria-label="Two colleagues giving a high five in an office"></div>

<footer class="site-footer">
  <div class="footer-brand"><i></i>quimbrosel</div>
  <p class="footer-tag">Sed ut perspiciatis unde omnis iste voluptatem accusantium doloreue</p>
  <div class="footer-follow">FOLLOW ON</div>
  <span class="footer-social" style="left:108px"><svg width="14" height="14" viewBox="0 0 14 14"><circle cx="7" cy="7" r="5.5" fill="none" stroke="#fff" stroke-width="1.6"/><circle cx="7" cy="7" r="2" fill="#fff"/></svg></span>
  <span class="footer-social" style="left:148px"><svg width="14" height="14" viewBox="0 0 14 14"><circle cx="7" cy="7" r="5.5" fill="none" stroke="#fff" stroke-width="1.6"/><circle cx="7" cy="7" r="2" fill="#fff"/></svg></span>
  <span class="footer-social" style="left:188px"><svg width="14" height="14" viewBox="0 0 14 14"><circle cx="7" cy="7" r="5.5" fill="none" stroke="#fff" stroke-width="1.6"/><circle cx="7" cy="7" r="2" fill="#fff"/></svg></span>
  <span class="footer-social" style="left:228px"><svg width="14" height="14" viewBox="0 0 14 14"><circle cx="7" cy="7" r="5.5" fill="none" stroke="#fff" stroke-width="1.6"/><circle cx="7" cy="7" r="2" fill="#fff"/></svg></span>

  <div class="col-title" style="left:464px">Quicklinks</div>
  <ul class="col-list" style="left:464px"><li>Home</li><li>About</li><li>Shop</li><li>Product</li><li>Science</li><li>Contact</li></ul>
  <div class="col-title" style="left:675px">Otherlinks</div>
  <ul class="col-list" style="left:675px"><li>Team</li><li>FAQ</li><li>Services</li><li>Privacy</li><li>Policy</li></ul>
  <div class="col-title" style="left:887px">Contact Us</div>

  <div class="contact-row" style="top:108px"><span class="contact-icon"><svg width="14" height="14" viewBox="0 0 14 14"><path d="M3 1l2 3-1.5 1.5a8 8 0 0 0 5 5L10 9l3 2-1.5 2.5C6 13 1 8 .5 2.5z" fill="none" stroke="#fff" stroke-width="1.3"/></svg></span>+1 555 014 2290</div>
  <div class="contact-row" style="top:170px"><span class="contact-icon"><svg width="14" height="11" viewBox="0 0 14 11"><rect x=".7" y=".7" width="12.6" height="9.6" rx="1" fill="none" stroke="#fff" stroke-width="1.3"/><path d="M1 1l6 5 6-5" fill="none" stroke="#fff" stroke-width="1.3"/></svg></span>info@quimbrosel.com</div>
  <div class="contact-row" style="top:232px"><span class="contact-icon"><svg width="12" height="15" viewBox="0 0 12 15"><path d="M6 14S1 8.5 1 5.5a5 5 0 0 1 10 0C11 8.5 6 14 6 14z" fill="none" stroke="#fff" stroke-width="1.3"/><circle cx="6" cy="5.5" r="1.8" fill="#fff"/></svg></span>123,Lorem ipsum dolor<br>consectetur adipiscing</div>

  <div class="footer-rule"></div>
  <p class="copyright">©Copyrights 2022&nbsp; Quimbrosel&nbsp;&nbsp; All Rights Reserved.</p>
</footer>

</body>
</html>
```